Business Cards for IT Consulting Company (Managed Service Provider)

I am looking to have some business cards printed and would like some designs. We are an IT Consulting company based in Vancouver BC. I would like a nice clean and modern look to the cards. I have uploaded all the versions of my logo so parts can be used as needed. Here is a snippit from our website homepage:

Quillbrook Networks Ltd. is an IT Solutions Partner located in Vancouver BC, Canada. We offer IT solutions and support to customers in the greater Vancouver Area. With expertise in Microsoft platforms, as well as Linux and Mac OSX and over 12 years experience in the IT industry, Quillbrook Networks is dedicated to offering our clients top quality service and products. We take pride in the solutions we offer our customers. The greatest compliment a client can give us is to recommend our services.

Quillbrook Networks Ltd. offers a wide range of IT services from onsite service to remote support and managed service solutions. This allows clients to choose the support path that best suits their company’s needs. Supporting many different sized companies from small to enterprise level over the past 12 years Quillbrook Networks has the experience and expertise needed to ensure things run smoothly. Allowing our clients to focus on doing business.

Revolutionizing the way IT services are delivered.

Quillbrook Networks is dedicated to providing our clients with IT solutions that work and grow with them for years to come. This philosophy helps save money in the long run instead of replacing equipment constantly. Far too often IT solutions are not well thought out and while possibly solving the problem at hand, require replacement due to growth or quality within a very short time frame. Quillbrook Networks takes pride in providing solutions that will last and be able to accommodate growth without the need for replacement.

Industry/Entity Type

Information Technology

Contact Information for Business Card

Quillbrook Networks Ltd.
(Employee Name)
Eml: (Employees Email Address)
Web: quillbrook.me
Ph: 604-555-0148

Font styles to use
Serif
Sans Serif

Requirements
Must have
• The Company logo and company colors.
Nice to have
• - Our tag line: "Revolutionizing IT Services" or "Revolutionizing the way IT services are delivered."
• - Also I really like the idea of nature and technology together blending which is sort of where my logo came from so integrating that somehow onto the business cards would be great.

```html
<!DOCTYPE html>
<html lang="en">
<head>
<meta charset="utf-8">
<title>Quillbrook Networks Ltd. — Business Cards</title>
<link rel="stylesheet" href="https://fonts.googleapis.com/css2?family=Open+Sans:wght@400;600;700&display=swap">
<style>
  :root {
    --stage: #3a3430;
    --card: #0d0d0e;
    --accent: #1ba6e4;
    --text-light: #f2f2f2;
    --rule: #1b8fc4;
  }
  * { box-sizing: border-box; margin: 0; padding: 0; }
  html, body {
    width: 1200px;
    height: 844px;
    overflow: hidden;
    background: var(--stage);
    font-family: "Open Sans", Arial, sans-serif;
  }
  .stage {
    position: relative;
    width: 1200px;
    height: 844px;
  }
  .card {
    position: absolute;
    top: 272px;
    width: 520px;
    height: 300px;
    background: var(--card);
    border-radius: 3px;
    box-shadow: 0 10px 28px rgba(0,0,0,.45);
    overflow: hidden;
  }
  .card--contact { left: 50px; }
  .card--brand { left: 630px; }

  .wordmark {
    position: absolute;
    display: flex;
    align-items: center;
    gap: 12px;
    color: var(--accent);
    font-weight: 700;
    white-space: nowrap;
  }
  .wordmark__mark {
    width: 22px;
    height: 22px;
    background: var(--accent);
  }
  .card--contact .wordmark { left: 40px; top: 70px; font-size: 25px; }
  .card--brand .wordmark { left: 50%; top: 92px; transform: translateX(-50%); font-size: 27px; }

  .rule {
    position: absolute;
    height: 1px;
    background: var(--rule);
  }

  /* contact side */
  .holder {
    position: absolute;
    right: 34px;
    top: 136px;
    color: var(--accent);
    font-size: 19px;
    font-weight: 600;
  }
  .card--contact .rule--name { left: 0; width: 322px; top: 150px; }
  .card--contact .rule--name-end { right: 0; width: 22px; top: 150px; }
  .card--contact .rule--base { left: 0; right: 0; top: 262px; }
  .contact-list {
    position: absolute;
    right: 34px;
    top: 176px;
    list-style: none;
    text-align: right;
  }
  .contact-list li {
    display: flex;
    justify-content: flex-end;
    align-items: center;
    gap: 9px;
    color: var(--text-light);
    font-size: 14px;
    line-height: 24px;
  }
  .contact-list svg { width: 11px; height: 11px; fill: var(--accent); }

  /* brand side */
  .tagline {
    position: absolute;
    left: 50%;
    top: 190px;
    transform: translateX(-50%);
    color: var(--accent);
    font-size: 14px;
    font-weight: 600;
    white-space: nowrap;
  }
  .card--brand .rule--left { left: 0; width: 150px; top: 216px; }
  .card--brand .rule--right { right: 0; width: 150px; top: 216px; }
  .card--brand .rule--tag { left: 150px; right: 150px; top: 216px; opacity: 0; }
</style>
</head>
<body>
<main class="stage">

  <section class="card card--contact" aria-label="Business card, contact side">
    <div class="wordmark"><span class="wordmark__mark"></span>Quillbrook Networks Ltd.</div>
    <div class="rule rule--name"></div>
    <div class="rule rule--name-end"></div>
    <p class="holder">Daniel Marsh</p>
    <ul class="contact-list">
      <li>604-555-0148
        <svg viewBox="0 0 24 24" aria-hidden="true"><path d="M6.6 10.8a15.1 15.1 0 0 0 6.6 6.6l2.2-2.2c.3-.3.7-.4 1-.2 1.1.4 2.3.6 3.6.6.6 0 1 .4 1 1V20c0 .6-.4 1-1 1C10.6 21 3 13.4 3 4c0-.6.4-1 1-1h3.5c.6 0 1 .4 1 1 0 1.3.2 2.5.6 3.6.1.3 0 .7-.2 1z"/></svg>
      </li>
      <li>info@quillbrook.me
        <svg viewBox="0 0 24 24" aria-hidden="true"><path d="M2 5h20v14H2z M3.5 6.5 12 13l8.5-6.5" fill="var(--accent)" stroke="var(--card)" stroke-width="1.5"/></svg>
      </li>
      <li>www.quillbrook.me
        <svg viewBox="0 0 24 24" aria-hidden="true"><circle cx="12" cy="12" r="10"/><path d="M2 12h20M12 2c3 3 3 17 0 20M12 2c-3 3-3 17 0 20" fill="none" stroke="var(--card)" stroke-width="1.5"/></svg>
      </li>
    </ul>
    <div class="rule rule--base"></div>
  </section>

  <section class="card card--brand" aria-label="Business card, brand side">
    <div class="wordmark"><span class="wordmark__mark"></span>Quillbrook Networks Ltd.</div>
    <div class="rule rule--left"></div>
    <p class="tagline">Revolutionizing IT Services</p>
    <div class="rule rule--right"></div>
  </section>

</main>
</body>
</html>
```